Fresh Dwelling Tract Guide needs a new Landing Page

I like to get a landing page or website with 2-3 pages to help target home buyers who are looking to buy homes from builders such as TW Residences, Morvik, P.L. Fennick, etc. The landing page/website to be non-cluttered and be able to explain to home buyers that there are many benefits to include me as their buyer's agent when they buy a brand new home from any builders.
I may want to incorporate a short explanation video (animated) on the landing page and then for the viewer to click on a button that will take them to another page where they can search for new homes from different builders.
Target Market(s)
Home buyers looking to buy brand new home from builders such as TW Residences, Morvik, P.L. Fennick, etc.
Industry/Entity Type
Real Estate
Number of Pages Required
2 page
Font styles to use
Requirements
Must have
- The landing page may have the explanation video at the bottom of the landing page (scrolled down) or there may be a CALL TO ACTION button that takes the viewer to the 2nd page to watch the explanation video. Once they watched the explanation video and are still interested, they can click on another CALL TO ACTION button that will take them to another website that they will be able to search for all the available new homes and register their contact information.
Should not have
- No clutters and no dark colors.

```html
<!DOCTYPE html>
<html lang="en">
<head>
<meta charset="utf-8">
<title>Fresh Dwelling Tract Guide</title>
<link href="https://fonts.googleapis.com/css2?family=Poppins:wght@600;700&family=Roboto:wght@400&display=swap" rel="stylesheet">
<style>
  :root {
    --sky-top: #5e9bd0;
    --sky: #8cc0e6;
    --foliage: #7fae7c;
    --foliage-soft: #a3c69a;
    --house-siding: #d8cfc0;
    --house-stone: #b9aa97;
    --lawn: #8fb57f;
    --veil: rgba(24, 52, 82, 0.32);
    --white: #ffffff;
    --ink: #1d2a36;
    --accent: #f26522;
    --footer-band: rgba(26, 48, 72, 0.5);
  }
  * { margin: 0; padding: 0; box-sizing: border-box; }
  html, body { width: 1200px; height: 720px; overflow: hidden; }
  body { font-family: "Poppins", sans-serif; color: var(--white); }
  .hero { position: relative; width: 1200px; height: 720px; overflow: hidden; }
  .hero-photo {
    position: absolute; inset: 0;
    background:
      radial-gradient(ellipse 38% 30% at 78% 72%, var(--house-siding) 0%, rgba(216,207,192,0) 75%),
      radial-gradient(ellipse 42% 30% at 28% 74%, var(--house-siding) 0%, rgba(216,207,192,0) 75%),
      radial-gradient(ellipse 30% 26% at 55% 62%, var(--house-stone) 0%, rgba(185,170,151,0) 75%),
      radial-gradient(ellipse 22% 40% at 90% 25%, var(--foliage) 0%, rgba(127,174,124,0) 70%),
      radial-gradient(ellipse 20% 30% at 48% 25%, var(--foliage) 0%, rgba(127,174,124,0) 70%),
      radial-gradient(ellipse 18% 32% at 10% 50%, var(--foliage) 0%, rgba(127,174,124,0) 70%),
      linear-gradient(180deg, var(--sky-top) 0%, var(--sky) 30%, var(--foliage-soft) 48%, var(--house-siding) 72%, var(--lawn) 100%);
  }
  .hero-veil { position: absolute; inset: 0; background: var(--veil); }
  .brand {
    position: absolute; left: 48px; top: 32px;
    font-weight: 700; font-size: 28px; line-height: 1.2;
    text-transform: uppercase; letter-spacing: 0.3px;
    display: flex; flex-direction: column;
  }
  .menu-toggle {
    position: absolute; left: 1098px; top: 31px; width: 38px;
    display: flex; flex-direction: column; align-items: center;
    text-decoration: none; color: var(--white);
  }
  .menu-circle { width: 37px; height: 37px; border-radius: 50%; background: var(--white); display: flex; align-items: center; justify-content: center; }
  .menu-label { margin-top: 5px; font-size: 10px; font-weight: 700; letter-spacing: 0.2px; }
  .play-button {
    position: absolute; left: 565px; top: 191px; width: 70px; height: 70px;
    border-radius: 50%; background: var(--white);
    display: flex; align-items: center; justify-content: center;
  }
  .intro-kicker, .intro-title {
    position: absolute; left: 0; right: 0; text-align: center; font-weight: 700;
    text-shadow: 0 2px 10px rgba(20, 40, 60, 0.35);
  }
  .intro-kicker { top: 288px; font-size: 30px; line-height: 38px; letter-spacing: -1px; }
  .intro-title { top: 322px; font-size: 48px; line-height: 60px; letter-spacing: -1.4px; }
  .cta {
    position: absolute; left: 464px; top: 408px; width: 273px; height: 47px;
    background: var(--accent); color: var(--white); text-decoration: none;
    display: flex; align-items: center; justify-content: center;
    font-size: 18px; font-weight: 700; letter-spacing: -0.4px; text-transform: uppercase;
  }
  .site-footer {
    position: absolute; left: 0; right: 0; top: 670px; height: 37px;
    background: var(--footer-band);
    display: flex; align-items: center; justify-content: center;
    font-family: "Roboto", sans-serif; font-size: 13px;
  }
</style>
</head>
<body>
  <main class="hero">
    <div class="hero-photo" role="img" aria-label="Photograph of a large new two-storey family home with stone front, bay window and garage, surrounded by tall green trees under a clear blue sky"></div>
    <div class="hero-veil"></div>

    <div class="brand">
      <span>Fresh</span>
      <span>Dwelling</span>
      <span>Tract Guide</span>
    </div>

    <a class="menu-toggle" href="#menu">
      <span class="menu-circle">
        <svg width="16" height="13" viewBox="0 0 16 13" aria-hidden="true">
          <rect x="0" y="0" width="16" height="2.6" rx="1.3" fill="#1d2a36"/>
          <rect x="0" y="5.2" width="16" height="2.6" rx="1.3" fill="#1d2a36"/>
          <rect x="0" y="10.4" width="16" height="2.6" rx="1.3" fill="#1d2a36"/>
        </svg>
      </span>
      <span class="menu-label">MENU</span>
    </a>

    <a class="play-button" href="#video" aria-label="Play explanation video">
      <svg width="30" height="34" viewBox="0 0 30 34" aria-hidden="true">
        <path d="M5 3 L27 17 L5 31 Z" fill="#111" stroke="#111" stroke-width="4" stroke-linejoin="round"/>
      </svg>
    </a>
    <p class="intro-kicker">WELCOME TO</p>
    <h1 class="intro-title">FRESH DWELLING TRACT GUIDE</h1>
    <a class="cta" href="#search">Search for new homes</a>

    <footer class="site-footer">Copyrights @ 2018 All Rights Reserved</footer>
  </main>
</body>
</html>
```